Brand new redesign of Brightpath finance website

I need a new website design that i can advertise a great low interest rate on the front page and capture input application details that will send through to my email address.

some car finance companies will be similar to this would be listed below

tallowcredit.example.com.au
mirabelfinance.example.com.au
finance725.example.com.au
quenbyfinance.example.com.au
finance91.example.com.au

Reason: I have changed the project to a committed project. all the webpages should have the same format just different content and i want to be able to edit the front page easily to update my interest rates.

Target Market(s)

Australian Finance market targeting a younger demographic

Industry/Entity Type

Finance

Coding

Coded - Design and coding required

Number of Pages Required

5+ page

Font styles to use
Serif
Sans Serif

Colors
0255a3
ffffff
cedeed

Requirements
Must have
• application capture form
• apply now buttons
• Headline rate front page

```html
<!DOCTYPE html>
<html lang="en">
<head>
<meta charset="utf-8">
<title>Brightpath Finance</title>
<link href="https://fonts.googleapis.com/css2?family=Roboto:wght@400;500;700&family=Lato:wght@400;700&display=swap" rel="stylesheet">
<style>
:root{
  --blue:#0255a3;
  --blue-dark:#04498f;
  --white:#ffffff;
  --pale:#cedeed;
  --ink:#222831;
  --muted:#444b55;
  --rule:#d5dbe2;
  --grey-btn:#e4e8ec;
}
*{box-sizing:border-box;margin:0;padding:0}
html,body{width:793px;height:1200px;overflow:hidden;background:var(--white)}
body{position:relative;font-family:'Lato',sans-serif;color:var(--ink)}
.abs{position:absolute}
.head{font-family:'Roboto',sans-serif}

/* top bar */
.topbar{left:0;top:0;width:793px;height:29px;background:var(--blue)}
.social{top:5px;width:20px;height:20px;border-radius:2px}
.apply-btn{left:549px;top:4px;width:70px;height:21px;background:var(--pale);color:#2a3a4c;font:400 11px 'Roboto',sans-serif;display:flex;align-items:center;justify-content:center}
.top-phone{left:637px;top:6px;color:var(--white);font:500 14px 'Roboto',sans-serif;display:flex;align-items:center;gap:5px}

/* nav */
.nav{left:0;top:29px;width:793px;height:80px;background:var(--white);border-bottom:1px solid #e3e6ea}
.nav-link{top:62px;font:400 11px 'Roboto',sans-serif;color:#333;letter-spacing:.2px}
.nav-link.active{color:var(--blue)}
.nav-sep{top:60px;width:1px;height:15px;background:#cfd4da}
.brand{left:340px;top:34px;width:113px;text-align:center}
.brand-mark{width:40px;height:40px;border-radius:50%;background:var(--blue);margin:0 auto 4px}
.brand-name{font:700 15px 'Roboto',sans-serif;color:var(--blue);line-height:1.05;letter-spacing:.5px}

/* hero */
.hero{left:0;top:109px;width:793px;height:309px;background:linear-gradient(120deg,#7d8a8f 0%,#a8a69b 35%,#c49478 55%,#6f7a63 80%,#3f4d35 100%)}
.hero-points{left:358px;top:180px;color:var(--white);font:400 11px 'Roboto',sans-serif;line-height:15px}
.hero-points li{list-style:none;margin-bottom:9px;padding-left:14px;position:relative}
.hero-points li::before{content:"»";position:absolute;left:0;font-size:10px}
.badge{left:430px;top:280px;width:102px;height:102px;border-radius:50%;border:3px solid rgba(255,255,255,.85)}
.arrow{top:250px}

.quote{left:552px;top:127px;width:188px;height:252px;background:rgba(206,222,237,.93)}
.quote-title{height:28px;background:var(--blue);color:var(--white);font:700 13px 'Roboto',sans-serif;padding:7px 0 0 12px}
.field{left:11px;width:165px;height:22px;background:var(--white);font:400 7.5px 'Lato',sans-serif;color:#8a9099;padding:7px 0 0 10px}
.check{left:12px;top:193px;width:10px;height:10px;background:var(--white);border:1px solid #c4ccd6}
.check-label{left:31px;top:194px;font:700 7.5px 'Lato',sans-serif;color:#3a4450}
.quote-btn{left:8px;top:217px;width:165px;height:27px;background:var(--blue);color:var(--white);font:700 12.5px 'Roboto',sans-serif;display:flex;align-items:center;justify-content:center}

/* intro */
.sec-title{font:400 21px 'Roboto',sans-serif;color:#3b4450;letter-spacing:.2px}
.sec-title b{font-weight:400;color:var(--blue)}
.sec-rule{height:1px;background:var(--rule)}
.sec-caret{width:0;height:0;border-left:5px solid transparent;border-right:5px solid transparent;border-top:5px solid var(--blue)}
.body-copy{left:54px;width:292px;font:400 9.2px 'Lato',sans-serif;line-height:15px;color:#2d333b}
.call{left:54px;top:617px;font:400 17px 'Roboto',sans-serif;color:#2d333b}
.call b{font:700 23px 'Roboto',sans-serif;color:var(--blue);margin-left:8px}
.vdiv{left:369px;top:470px;width:1px;height:190px;background:#e2e6ea}
.loan-icon{width:36px;height:36px;border-radius:50%;background:var(--blue)}
.loan-name{font:500 14px 'Roboto',sans-serif;color:#222}
.loan-desc{width:125px;font:400 8px 'Lato',sans-serif;line-height:11.5px;color:#333}

/* repayments */
.repay{left:0;top:691px;width:793px;height:159px;background:linear-gradient(90deg,#3a3834 0%,#55534e 40%,#4a4c4f 70%,#34383c 100%)}
.band-title{color:var(--white);font:400 30px 'Roboto',sans-serif}
.band-sub{color:var(--white);font:400 15.5px 'Roboto',sans-serif}
.btn-blue{left:582px;top:753px;width:147px;height:35px;background:var(--blue);color:var(--white);font:500 17px 'Roboto',sans-serif;display:flex;align-items:center;justify-content:center}

/* approval */
.approval{left:0;top:850px;width:793px;height:158px;background:var(--blue)}
.btn-grey{left:593px;top:906px;width:135px;height:35px;background:var(--grey-btn);color:#2a2f36;font:500 16px 'Roboto',sans-serif;display:flex;align-items:center;justify-content:center}

/* footer */
.footer{left:0;top:1008px;width:793px;height:192px;background:var(--pale)}
.foot-mark{left:72px;top:1039px;width:100px;height:92px;border-radius:50%;background:linear-gradient(135deg,#c9ccd0,#8d9196)}
.foot-phone{left:70px;top:1148px;font:500 16px 'Roboto',sans-serif;color:var(--blue)}
.foot-vline{left:209px;top:1035px;width:0;height:140px;border-left:1px dashed #b3c2d2}
.foot-links{left:243px;top:1051px;width:495px;display:flex;justify-content:space-between;font:400 11.5px 'Roboto',sans-serif;color:#222}
.foot-links span.sl{color:#333}
.foot-icon{width:35px;height:35px;border-radius:50%;background:var(--blue);display:flex;align-items:center;justify-content:center}
.foot-text{font:400 10.5px 'Roboto',sans-serif;color:#222;line-height:14px}
.foot-text.small{font-size:9px}
.foot-dline{left:277px;top:1145px;width:440px;border-top:1px dashed #b3c2d2}
.foot-cvl{top:1085px;height:50px;border-left:1px dashed #b3c2d2}
.copyright{left:0;width:793px;padding-left:200px;top:1158px;text-align:center;font:400 9px 'Lato',sans-serif;color:#222}
.foot-bottom{left:0;top:1197px;width:793px;height:3px;background:var(--blue)}
</style>
</head>
<body>

<!-- top bar -->
<div class="abs topbar"></div>
<div class="abs social" style="left:53px;background:#3b5e9e" role="img" aria-label="Social link"></div>
<div class="abs social" style="left:81px;background:#3fa9e6" role="img" aria-label="Social link"></div>
<div class="abs social" style="left:108px;background:#c4302b" role="img" aria-label="Social link"></div>
<div class="abs apply-btn">APPLY NOW</div>
<div class="abs top-phone">
  <svg width="11" height="11" viewBox="0 0 24 24"><path fill="#fff" d="M6.6 10.8a15.2 15.2 0 0 0 6.6 6.6l2.2-2.2c.3-.3.7-.4 1-.2 1.1.4 2.3.6 3.6.6.6 0 1 .4 1 1V20c0 .6-.4 1-1 1A17 17 0 0 1 3 4c0-.6.4-1 1-1h3.5c.6 0 1 .4 1 1 0 1.3.2 2.5.6 3.6.1.3 0 .7-.2 1z"/></svg>
  555-010-2468
</div>

<!-- nav -->
<div class="abs nav"></div>
<div class="abs nav-link active" style="left:71px">HOME</div>
<div class="abs nav-sep" style="left:126px"></div>
<div class="abs nav-link" style="left:152px">ABOUT US</div>
<div class="abs nav-sep" style="left:227px"></div>
<div class="abs nav-link" style="left:252px">LOANS
  <svg width="9" height="6" viewBox="0 0 9 6" style="margin-left:4px"><path d="M1 1l3.5 3.5L8 1" fill="none" stroke="#555" stroke-width="1.2"/></svg>
</div>
<div class="abs brand">
  <div class="brand-mark"></div>
  <div class="brand-name">BRIGHTPATH<br>FINANCE</div>
</div>
<div class="abs nav-link" style="left:466px">INSURANCE</div>
<div class="abs nav-sep" style="left:532px"></div>
<div class="abs nav-link" style="left:541px">FINANCE CALCULATOR</div>
<div class="abs nav-sep" style="left:664px"></div>
<div class="abs nav-link" style="left:673px">CONTACT US</div>

<!-- hero -->
<div class="abs hero" role="img" aria-label="Photo of a smiling young family standing in front of their house"></div>
<ul class="abs hero-points">
  <li>Low Rate Car Loans From 4.69%<br>Comparison Rate 4.99%</li>
  <li>Low Fees</li>
  <li>Low Total Cost Loans</li>
</ul>
<div class="abs badge" role="img" aria-label="Low rate guarantee seal"></div>
<svg class="abs arrow" style="left:22px" width="14" height="24" viewBox="0 0 14 24"><path d="M12 2L2 12l10 10" fill="none" stroke="#fff" stroke-width="2.5"/></svg>
<svg class="abs arrow" style="left:757px" width="14" height="24" viewBox="0 0 14 24"><path d="M2 2l10 10L2 22" fill="none" stroke="#fff" stroke-width="2.5"/></svg>

<form class="abs quote">
  <div class="quote-title">QUICK &amp; EASY QUOTE</div>
  <div class="abs field" style="top:38px">First Name</div>
  <div class="abs field" style="top:67px">Last Name</div>
  <div class="abs field" style="top:98px">Email Address</div>
  <div class="abs field" style="top:128px">Phone Number</div>
  <div class="abs field" style="top:158px">Loan Amount In Dollars
    <svg class="abs" style="right:9px;top:8px" width="8" height="5" viewBox="0 0 8 5"><path d="M1 1l3 3 3-3" fill="none" stroke="#777" stroke-width="1"/></svg>
  </div>
  <div class="abs check"></div>
  <div class="abs check-label">I Agree To The Terms &amp; Conditions</div>
  <div class="abs quote-btn">GET MY BEST RATE NOW</div>
</form>

<!-- online loan pre approval -->
<div class="abs sec-title" style="left:54px;top:450px"><b>ONLINE LOAN</b> PRE APPROVAL</div>
<div class="abs sec-rule" style="left:54px;top:480px;width:288px"></div>
<div class="abs sec-caret" style="left:81px;top:480px"></div>
<p class="abs body-copy" style="top:501px">Sed ut perspiciatis unde omnis iste natus error sit voluptatem accusantium dolo remque laudantium, totam rem aperiam, eaque ipsa quae ab illo inventore veritatis et quasi architecto beatae vitae dicta sunt explicabo. Sed ut perspiciatis unde omnis iste natus error sit volu. eaque ipsa quae ab illo inventore veritatis et quasi architecto.</p>
<p class="abs body-copy" style="top:581px;letter-spacing:.2px">Sed ut perspiciatis unde omnis iste natus error sit voluptatem accusantium dolo remque laudantium.</p>
<div class="abs call">Call Today<b>1300 555 019</b></div>
<div class="abs vdiv"></div>

<!-- loans -->
<div class="abs sec-title" style="left:393px;top:450px"><b>WE PROVIDE</b> LOANS FOR</div>
<div class="abs sec-rule" style="left:393px;top:480px;width:348px"></div>
<div class="abs sec-caret" style="left:420px;top:480px"></div>

<div class="abs loan-icon" style="left:390px;top:507px">
  <svg width="36" height="36" viewBox="0 0 36 36"><path fill="#fff" d="M11 20l2-6h10l2 6v5h-2v-2H13v2h-2z"/><circle cx="14" cy="21" r="1.2" fill="#0255a3"/><circle cx="22" cy="21" r="1.2" fill="#0255a3"/></svg>
</div>
<div class="abs loan-name" style="left:437px;top:510px">VEHICLES</div>
<div class="abs loan-desc" style="left:437px;top:535px">Sed ut perspiciatis unde omnis iste natus error sit volupta perspiciatis unde .</div>

<div class="abs loan-icon" style="left:575px;top:507px">
  <svg width="36" height="36" viewBox="0 0 36 36"><path fill="#fff" d="M13 13h10v6H13z M10 20h16l-3 5H13z"/></svg>
</div>
<div class="abs loan-name" style="left:622px;top:510px">BOAT</div>
<div class="abs loan-desc" style="left:622px;top:535px">Sed ut perspiciatis unde omnis iste natus error sit volupta perspiciatis unde .</div>

<div class="abs loan-icon" style="left:390px;top:594px">
  <svg width="36" height="36" viewBox="0 0 36 36"><path fill="#fff" d="M18 10l9 8h-3v7h-4v-5h-4v5h-4v-7H9z"/></svg>
</div>
<div class="abs loan-name" style="left:437px;top:598px">HOME</div>
<div class="abs loan-desc" style="left:437px;top:623px">Sed ut perspiciatis unde omnis iste natus error sit volupta perspiciatis unde .</div>

<div class="abs loan-icon" style="left:575px;top:594px">
  <svg width="36" height="36" viewBox="0 0 36 36"><circle cx="18" cy="14" r="4" fill="#fff"/><path fill="#fff" d="M11 27v-4c0-3 3-4 7-4s7 1 7 4v4z"/></svg>
</div>
<div class="abs loan-name" style="left:622px;top:598px">PERSONAL</div>
<div class="abs loan-desc" style="left:622px;top:623px">Sed ut perspiciatis unde omnis iste natus error sit volupta perspiciatis unde .</div>

<!-- repayments -->
<div class="abs repay" role="img" aria-label="Blurred photo of a couple reviewing finances at home"></div>
<div class="abs band-title" style="left:55px;top:740px">WHAT WILL MY REPAYMENTS BE?</div>
<div class="abs band-sub" style="left:55px;top:783px">See how much you could borrow with our loan calculator.</div>
<div class="abs btn-blue">Loan Calculator</div>

<!-- approval -->
<div class="abs approval"></div>
<div class="abs band-title" style="left:54px;top:892px;font-size:23px">Find out what Guaranteed Approval Actually means</div>
<div class="abs band-sub" style="left:55px;top:928px">See how much you could borrow with our loan calculator.</div>
<div class="abs btn-grey">Find Out More</div>

<!-- footer -->
<div class="abs footer"></div>
<div class="abs foot-mark"></div>
<div class="abs foot-phone">1300 555 019</div>
<div class="abs foot-vline"></div>
<nav class="abs foot-links">
  <span>Home</span><span class="sl">/</span><span>About Us</span><span class="sl">/</span><span>Loans</span><span class="sl">/</span><span>Insurance</span><span class="sl">/</span><span>Finance Calculator</span><span class="sl">/</span><span>Contact Us</span>
</nav>

<div class="abs foot-icon" style="left:237px;top:1090px">
  <svg width="14" height="18" viewBox="0 0 14 18"><path fill="#fff" d="M7 0a7 7 0 0 0-7 7c0 5 7 11 7 11s7-6 7-11a7 7 0 0 0-7-7zm0 9.5A2.5 2.5 0 1 1 7 4.5a2.5 2.5 0 0 1 0 5z"/></svg>
</div>
<div class="abs foot-text" style="left:282px;top:1091px">BRIGHTPATH FINANCE<br>48 Example Lane<br>Parkvale QA 5678</div>
<div class="abs foot-cvl" style="left:405px"></div>

<div class="abs foot-icon" style="left:423px;top:1090px">
  <svg width="16" height="16" viewBox="0 0 24 24"><path fill="#fff" d="M6.6 10.8a15.2 15.2 0 0 0 6.6 6.6l2.2-2.2c.3-.3.7-.4 1-.2 1.1.4 2.3.6 3.6.6.6 0 1 .4 1 1V20c0 .6-.4 1-1 1A17 17 0 0 1 3 4c0-.6.4-1 1-1h3.5c.6 0 1 .4 1 1 0 1.3.2 2.5.6 3.6.1.3 0 .7-.2 1z"/></svg>
</div>
<div class="abs foot-text" style="left:468px;top:1091px">Call Us<br>1300 555 019</div>
<div class="abs foot-cvl" style="left:553px"></div>

<div class="abs foot-icon" style="left:572px;top:1090px">
  <svg width="18" height="13" viewBox="0 0 18 13"><rect x="0.5" y="0.5" width="17" height="12" fill="none" stroke="#fff"/><path d="M1 1l8 6 8-6M1 12l6-5M17 12l-6-5" fill="none" stroke="#fff"/></svg>
</div>
<div class="abs foot-text" style="left:616px;top:1091px">Email<br><span class="small">info@brightpathfinance.example.com</span></div>

<div class="abs foot-dline"></div>
<div class="abs copyright">Copyright © 2016 BRIGHTPATH FINANCE. All Rights Reserved.</div>
<div class="abs foot-bottom"></div>

</body>
</html>
```